Halvik - consultancy website

I need a new design for my webpage/presence [to be functioning with Wordpress - I have a programmer to set it up but not the design idea].
My company is Halvik - a consultancy firm focused on growth management for Swedish SME's primarily;. We call it Leadership toolkit for firms on the rise, kind of a doctor helping small become big. Contentwise, its a simple frontpage + 3-4 subpages with content re company/myself/focus etc. The new site should communicate a fresh, trustworthy take yet simple and functional on all devices [i.e. think UI compatible for mobile/tablet]. Current building parts/form elements are
a) existing logo and text elements
b) existing pictures
c) the yellowish color
colours and new ideas on pictures/positioning are welcome. I prefer a 'full width page' solution with centralised text elements but that's all up to you to suggest. Current site is a quickfix made by myself - now I'm moving it to a new platform so want to take the opportunity to make it
Nothing superspecial as it is a 2-man show; on the other hand I still want to have a modern & fresh reflection of my brand in digital environments. Help me out!
www.halvik-demo.se
Best
Lina Bergqvist

```html
<!DOCTYPE html>
<html lang="en">
<head>
<meta charset="utf-8">
<title>Halvik – Growth management consultancy</title>
<link rel="stylesheet" href="https://fonts.googleapis.com/css2?family=Crimson+Text&family=Open+Sans:wght@400;600&display=swap">
<style>
:root{
  --orange:#f0a23b;
  --ink:#222;
  --text:#555;
  --muted:#999;
  --light:#f2f2f2;
  --card:#f7f7f7;
  --footer:#2c2c2c;
  --footer-base:#262626;
  --blue:#3b5a9a;
  --sky:#2aa9e0;
  --red:#de4b39;
}
*{margin:0;padding:0;box-sizing:border-box}
html,body{width:819px;height:1200px;overflow:hidden;background:#fff}
body{position:relative;font-family:"Open Sans",sans-serif;color:var(--text)}
.abs{position:absolute}

.brand{left:67px;top:16px}
.brand-name{font-family:"Crimson Text",serif;font-size:38px;line-height:1;color:var(--ink)}
.brand-tag{font-family:"Crimson Text",serif;font-size:11.5px;color:var(--ink);margin-top:2px;padding-left:2px}

.nav{left:396px;top:34px;display:flex;gap:4px}
.nav a{display:block;width:72px;height:26px;line-height:26px;text-align:center;font-size:9px;color:var(--ink);background:var(--light);text-decoration:none}
.nav a.is-active{background:var(--orange);color:#fff}

.hero{left:0;top:92px;width:819px;height:306px;background:var(--orange);box-shadow:0 6px 10px rgba(0,0,0,.08)}
.hero-photo{position:absolute;left:0;top:0;width:303px;height:306px;background:linear-gradient(90deg,#efefef,#f6f6f6 70%,#e8e3dc)}
.hero-title{position:absolute;right:76px;top:107px;width:380px;text-align:right;color:#fff;font-size:18.5px;line-height:21px;font-weight:400}
.hero-btn{position:absolute;left:670px;top:165px;width:72px;height:22px;line-height:22px;background:#111;color:#fff;font-size:9.5px;font-weight:600;text-align:center}
.hero-dots{position:absolute;left:773px;top:283px;display:flex;gap:4px}
.hero-dots span{width:6px;height:6px;border-radius:50%;border:1px solid #222}
.hero-dots span.on{background:#222}

.welcome-title{left:0;width:819px;top:428px;text-align:center;font-size:18px;color:var(--ink);font-weight:400}
.welcome-text{left:72px;width:675px;top:466px;text-align:center;font-size:8.2px;line-height:13px}

.about-photo{left:67px;top:524px;width:163px;height:105px;background:linear-gradient(180deg,#a9a89a,#8c8877 60%,#6e6a5c)}
.tabs{left:247px;top:521px;display:flex;font-size:9.6px;color:#777}
.tabs span{margin-right:26px}
.tabs .is-active{color:var(--ink)}
.about-text{left:250px;top:555px;width:490px;font-size:8.2px;line-height:12.3px}
.about-text p+p{margin-top:12px}

.projects-title{left:66px;top:692px;font-size:17.5px;color:var(--ink);font-weight:400}
.arrows{left:715px;top:696px;display:flex;gap:3px}
.arrows span{width:17px;height:15px;display:flex;align-items:center;justify-content:center}
.arrows .prev{background:var(--orange)}
.arrows .next{background:#222}

.projects{left:67px;top:740px;display:flex}
.project{width:171px;height:204px;background:var(--card)}
.project-img{height:155px}
.project-body{padding:13px 16px}
.project-name{font-size:8.6px;font-weight:600;color:var(--ink)}
.project-cat{font-size:5.4px;color:var(--muted);margin-top:6px;letter-spacing:.2px}
.project.is-active{background:var(--orange)}
.project.is-active .project-name,.project.is-active .project-cat{color:#fff}

.footer{left:0;top:1010px;width:819px;height:156px;background:var(--footer)}
.footer-base{left:0;top:1166px;width:819px;height:34px;background:var(--footer-base);text-align:center;font-size:7px;color:#777;line-height:36px}
.f-head{position:absolute;font-size:8.6px;font-weight:600;color:#eee}
.divider{position:absolute;top:30px;width:1px;height:106px;background:#3c3c3c}
.socials{position:absolute;left:67px;top:59px;display:flex;gap:5px}
.social{width:49px;height:64px;color:#fff;font-size:8.6px;text-align:center;padding-top:12px}
.social i{display:block;width:26px;height:26px;border-radius:50%;background:rgba(255,255,255,.15);margin:0 auto 11px}
.fb{background:var(--blue)}.tw{background:var(--sky)}.gp{background:var(--red)}
.mail-text{position:absolute;left:366px;top:56px;width:160px;font-size:7.5px;line-height:13px;color:#999}
.mail-form{position:absolute;left:366px;top:89px;display:flex}
.mail-input{width:136px;height:19px;background:#fff;font-size:6.5px;color:#aaa;line-height:19px;padding-left:11px}
.mail-btn{width:22px;height:19px;background:var(--orange);display:flex;align-items:center;justify-content:center}
.mail-note{position:absolute;left:366px;top:116px;font-size:6.8px;color:#666}
.menu{position:absolute;left:664px;top:57px;list-style:none;font-size:7.5px;line-height:14.6px;color:#ccc}
</style>
</head>
<body>

<header>
  <div class="abs brand">
    <div class="brand-name">Halvik.</div>
    <div class="brand-tag">Leadership toolkit for firms on the rise</div>
  </div>
  <nav class="abs nav">
    <a class="is-active" href="#">Home</a><a href="#">About Us</a><a href="#">Services</a><a href="#">Clients</a><a href="#">Contact Us</a>
  </nav>
</header>

<section class="abs hero">
  <div class="hero-photo" role="img" aria-label="Photo of a child standing against a wall marked with height lines"></div>
  <h1 class="hero-title">We are a consultancy firm focused on growth management for Swedish SME's</h1>
  <div class="hero-btn">Read More</div>
  <div class="hero-dots"><span class="on"></span><span></span><span></span></div>
</section>

<h2 class="abs welcome-title">WELCOME</h2>
<p class="abs welcome-text">Nunc aliquam leo nec diam pellentesque hendrerit. Vestibulum eu neque eget ex luctus efficitur vitae quis nunc. Maecenas porta rhoncus mauris, sed pharetra purus euismod tempor. Donec pulvinar, turpis eu consectetur egestas, dui diam suscipit</p>

<div class="abs about-photo" role="img" aria-label="Vintage photo of a child lifting a toy barbell"></div>
<div class="abs tabs"><span class="is-active">What we do</span><span>|</span><span>Who we are</span><span>|</span><span>Why Halvik</span></div>
<div class="abs about-text">
  <p>1] We work side by side with owners and leadership teams of small and mid-sized companies, turning growth plans into clear priorities, roles and routines. Our approach is hands-on and practical, giving structure where it is needed and room where it matters, so the business can scale with confidence. Leadership toolkit for growing companies</p>
  <p>2] An independent consultancy firm specializing in growth management; realizing your strategy into concrete actions and metrics to help you get ahead.</p>
</div>

<h2 class="abs projects-title">LATEST PROJECTS</h2>
<div class="abs arrows">
  <span class="prev"><svg width="6" height="8" viewBox="0 0 6 8"><path d="M5 1 2 4l3 3" fill="none" stroke="#fff" stroke-width="1.3"/></svg></span>
  <span class="next"><svg width="6" height="8" viewBox="0 0 6 8"><path d="M1 1l3 3-3 3" fill="none" stroke="#fff" stroke-width="1.3"/></svg></span>
</div>
<div class="abs projects">
  <div class="project"><div class="project-img" role="img" aria-label="Photo of hands on a laptop with sketched diagrams" style="background:linear-gradient(180deg,#e6e4df,#9a9893 70%,#2b2b2b)"></div><div class="project-body"><div class="project-name">Lagoon Art Pavilion</div><div class="project-cat">FASHION / BUSINESS</div></div></div>
  <div class="project is-active"><div class="project-img" role="img" aria-label="Photo of a business team reviewing documents" style="background:linear-gradient(135deg,#c9d6dc,#b8b3aa 55%,#4a4e57)"></div><div class="project-body"><div class="project-name">Large Poster Set</div><div class="project-cat">PRINT / MEDIA</div></div></div>
  <div class="project"><div class="project-img" role="img" aria-label="Photo of hands working over paperwork and charts" style="background:linear-gradient(180deg,#dfe0e0,#c8c9ca 60%,#e9eaea)"></div><div class="project-body"><div class="project-name">Marlow Branding</div><div class="project-cat">GRAPHIC / DESIGN</div></div></div>
  <div class="project"><div class="project-img" role="img" aria-label="Photo of a hand holding a glowing blue globe" style="background:radial-gradient(circle at 55% 40%,#6fc4f2,#1c5fa8 45%,#0c2247)"></div><div class="project-body"><div class="project-name">Promotional Tags</div><div class="project-cat">ART / LOGO</div></div></div>
</div>

<footer class="abs footer">
  <div class="f-head" style="left:67px;top:32px">Let's Connect</div>
  <div class="socials">
    <div class="social fb"><i></i>2598</div>
    <div class="social tw"><i></i>4576</div>
    <div class="social gp"><i></i>1269</div>
  </div>
  <div class="divider" style="left:298px"></div>
  <div class="f-head" style="left:366px;top:33px">Mailing List</div>
  <p class="mail-text">Sign up for our mailing list to get latest updates and offers.</p>
  <div class="mail-form">
    <div class="mail-input">Email address</div>
    <div class="mail-btn"><svg width="9" height="7" viewBox="0 0 9 7"><path d="M1 3.5l2.4 2.3L8 1" fill="none" stroke="#fff" stroke-width="1.5"/></svg></div>
  </div>
  <div class="mail-note">We respect your privacy</div>
  <div class="divider" style="left:597px"></div>
  <div class="f-head" style="left:664px;top:33px">Menu</div>
  <ul class="menu"><li>Home</li><li>About Us</li><li>Services</li><li>Gallery</li><li>Contact Us</li></ul>
</footer>
<div class="abs footer-base">© COPYRIGHTS 2015 ALL RIGHTS RESERVED</div>

</body>
</html>
```